We need a logo for our business which is a dental clinic (i.e. dentistry).
We would lilke designs using the colour blue, green and black incorporating the words Corvath Dental, possibly a smile or a tooth image can be considered for incorporation in the logo.

Industry/Entity Type

Dental

```html
<!DOCTYPE html>
<html lang="en">
<head>
<meta charset="utf-8">
<title>Corvath Dental – Business Card</title>
<link rel="stylesheet" href="https://fonts.googleapis.com/css2?family=Marcellus&family=Source+Sans+3:wght@400&display=swap">
<style>
  :root {
    --paper: #ffffff;
    --brand-blue: #25a8df;
    --name-blue: #1ba7e2;
    --brand-green: #8cc63f;
    --ink-grey: #555759;
    --divider: #e6e6e6;
  }
  html, body {
    margin: 0;
    padding: 0;
    overflow: hidden;
    background: var(--paper);
  }
  .card {
    position: relative;
    width: 1200px;
    height: 686px;
    overflow: hidden;
    background: var(--paper);
  }
  .card-wave {
    position: absolute;
    inset: 0;
    width: 1200px;
    height: 686px;
  }
  .wave-accent { fill: var(--brand-green); }
  .wave-base { fill: var(--brand-blue); }

  .brand-name {
    position: absolute;
    left: 114px;
    top: 62px;
    margin: 0;
    font-family: "Marcellus", serif;
    font-weight: 400;
    font-size: 74px;
    line-height: 1;
    color: var(--name-blue);
    letter-spacing: 0.5px;
  }

  .person {
    position: absolute;
    left: 0;
    top: 364px;
    width: 1200px;
    text-align: center;
  }
  .person-name {
    margin: 0;
    font-family: "Marcellus", serif;
    font-weight: 400;
    font-size: 42px;
    line-height: 1;
    color: var(--name-blue);
  }
  .person-role {
    margin: 14px 0 0;
    font-family: "Source Sans 3", sans-serif;
    font-size: 25px;
    line-height: 1;
    color: var(--ink-grey);
  }

  .contact-bar {
    position: absolute;
    left: 0;
    top: 614px;
    height: 54px;
    display: flex;
    align-items: center;
    font-family: "Source Sans 3", sans-serif;
    font-size: 29px;
    color: var(--paper);
    white-space: nowrap;
  }
  .contact-item { position: absolute; top: 50%; transform: translateY(-50%); }
  .contact-phone { left: 138px; }
  .contact-email { left: 403px; }
  .contact-address { left: 818px; }
  .contact-divider {
    position: absolute;
    top: 0;
    width: 4px;
    height: 54px;
    background: var(--divider);
  }
  .divider-one { left: 373px; }
  .divider-two { left: 795px; }
</style>
</head>
<body>
  <main class="card">
    <svg class="card-wave" viewBox="0 0 1050 600" preserveAspectRatio="none" aria-hidden="true">
      <path class="wave-accent" d="M0,296 C150,446 320,498 480,497 C700,496 950,370 1050,158 L1050,600 L0,600 Z"/>
      <path class="wave-base" d="M0,312 C150,456 320,509 480,508 C710,506 965,392 1050,222 L1050,600 L0,600 Z"/>
    </svg>

    <h1 class="brand-name">Corvath Dental</h1>

    <section class="person">
      <p class="person-name">Name Lastname</p>
      <p class="person-role">Dentist</p>
    </section>

    <footer class="contact-bar">
      <span class="contact-item contact-phone">Ph: xxx xxx xxx</span>
      <span class="contact-divider divider-one"></span>
      <span class="contact-item contact-email">corvathdental@mail.com</span>
      <span class="contact-divider divider-two"></span>
      <span class="contact-item contact-address">Address:</span>
    </footer>
  </main>
</body>
</html>
```